Website design for luxury private hair salon

I'm looking for someone to use my Logo and build me a website for my webpage www.corsetresses.com.au (You can have a look at it as it has every detail I need included on it already), however I want a fresh new appearance and it to look and feel super stylish.

I am thinking colours in black, with silver or white, beautiful hair images like the ones you'll see on the current webpage - the price list as per what you already see.

I will include a copy of my biz card on here, so you can see the feel of the card, and design a website with a similar feel. It is matt black with a foil silver.

Modern, but classic and fresh. I will also need you to be able to publish it to my URL for me as I have no idea how to do this. I need it up and running pronto!

The website will need to be able to be read clearly on all devices incluing smart phones and ipads. The URL is currently registered and hosted by Norvel Web

Thinking a Home Page - large logo etc and write up on who and what we offer
Services/Price List page - as per the price list on my current webpage
Contact Page - with a built in contact form.

Target Market(s)

Middle aged, fashionable, stylish women and men who enjoy luxury hair care and styling in an upmarket location.

Industry/Entity Type

Hair And Beauty

Number of Pages Required

3 page

Font styles to use
Other font styles liked:
• see my images for my current logo

Colors
000000
b2b2b2
a54499

Requirements
Must have
• Style
• Fast turnaround
• Be viewable on all devices, PC, ipads, smart phones
• Designer able to upload it so its a running website for me to my URL
Nice to have
• Just a really feminine, stylish website which is easy to read and shows some beautiful images of perfect hair
Should not have
• Browns, reds or orange colours.

```html
<!DOCTYPE html>
<html lang="en">
<head>
<meta charset="utf-8">
<title>Corsetresses — Private Luxury Hair Salon</title>
<link href="https://fonts.googleapis.com/css2?family=Nunito+Sans:wght@400;600;700&display=swap" rel="stylesheet">
<style>
  :root {
    --purple: #a54499;
    --purple-dark: #8e3784;
    --black: #000000;
    --ink: #2b2b2b;
    --grey-text: #8a8a8a;
    --silver: #b2b2b2;
    --band-grey: #d2d2d2;
    --footer-bg: #f4f4f4;
    --white: #ffffff;
  }
  * { box-sizing: border-box; margin: 0; padding: 0; }
  html, body { width: 1200px; height: 2486px; overflow: hidden; }
  body {
    position: relative;
    background: var(--white);
    font-family: "Nunito Sans", Arial, sans-serif;
    color: var(--ink);
  }
  .abs { position: absolute; }

  /* Hero */
  .hero {
    position: absolute; left: 0; top: 0; width: 1200px; height: 572px;
    background:
      linear-gradient(180deg, rgba(0,0,0,0.55) 0%, rgba(0,0,0,0) 30%),
      linear-gradient(115deg, #1a1a1a 0%, #3b3128 30%, #6b5a44 48%, #2a2521 62%, #7a6236 82%, #3a3020 100%);
  }
  .nav a {
    position: absolute; top: 74px; color: var(--white); font-size: 18px;
    text-decoration: none; letter-spacing: 0.5px; text-transform: uppercase;
  }
  .nav .sep { position: absolute; top: 74px; width: 1px; height: 22px; background: rgba(255,255,255,0.6); }
  .brand-hero {
    position: absolute; top: 68px; left: 470px; width: 260px; text-align: center;
    color: var(--white); font-size: 30px; font-weight: 400; letter-spacing: 1px; line-height: 36px;
  }
  .hero-title {
    position: absolute; top: 248px; left: 0; width: 1200px; text-align: center;
    color: var(--white); font-size: 46px; font-weight: 700; line-height: 48px; letter-spacing: 1px;
  }
  .dots { position: absolute; display: flex; gap: 9px; }
  .dots span { width: 14px; height: 14px; border-radius: 50%; background: var(--white); border: 2px solid var(--white); }
  .dots span.off { background: transparent; }

  /* Who we are */
  .who-photo {
    position: absolute; left: 199px; top: 583px; width: 348px; height: 408px;
    background: linear-gradient(160deg, #f1e2d0 0%, #d6a878 35%, #a86f45 70%, #e9d2bb 100%);
  }
  .section-title { font-size: 30px; font-weight: 400; color: var(--purple); letter-spacing: 0.5px; }
  .who-title { position: absolute; left: 600px; top: 678px; }
  .who-text {
    position: absolute; left: 600px; top: 736px; width: 470px;
    font-size: 14.5px; line-height: 27px; color: var(--grey-text);
  }
  .btn-read {
    position: absolute; left: 600px; top: 888px; width: 124px; height: 37px;
    background: linear-gradient(var(--purple), var(--purple-dark)); color: var(--white);
    font-size: 12px; font-weight: 700; text-align: center; line-height: 37px; border-radius: 3px;
  }

  /* What we offer */
  .offer-title { position: absolute; top: 1040px; left: 0; width: 1200px; text-align: center; font-size: 26px; font-weight: 400; color: var(--ink); }
  .offer-card { position: absolute; top: 1094px; width: 322px; height: 248px; color: var(--white); text-align: center; }
  .offer-card .name { position: absolute; top: 112px; width: 100%; font-size: 24px; }
  .offer-card .desc { position: absolute; top: 146px; width: 100%; font-size: 13px; line-height: 18px; }
  .offer-card .link { position: absolute; top: 192px; left: 120px; width: 82px; font-size: 14px; padding-bottom: 4px; border-bottom: 1px solid rgba(255,255,255,0.8); }
  .arrow { position: absolute; top: 1190px; width: 34px; height: 56px; background: rgba(255,255,255,0.9); }

  /* Products */
  .products-title { position: absolute; top: 1468px; left: 0; width: 1200px; text-align: center; font-size: 27px; }
  .products-text { position: absolute; top: 1512px; left: 250px; width: 700px; text-align: center; font-size: 15px; line-height: 26px; color: var(--grey-text); }
  .btn-outline {
    position: absolute; top: 1582px; left: 524px; width: 185px; height: 36px;
    border: 1px solid var(--silver); font-size: 15px; text-align: center; line-height: 34px; color: var(--ink); border-radius: 2px;
  }
  .products-shelf {
    position: absolute; top: 1660px; left: 180px; width: 850px; height: 140px;
    background: linear-gradient(90deg, #e6e9df 0%, #dfe3d8 22%, #b79ad0 34%, #cdb3e0 40%, #f0a64a 50%, #f4b860 58%, #3fb6c2 66%, #6fd0d8 74%, #d9d9d9 80%, #1f1f1f 86%, #c8232d 91%, #1f1f1f 100%);
  }

  /* Testimonials */
  .testi-title { position: absolute; top: 1836px; left: 0; width: 1200px; text-align: center; font-size: 27px; font-weight: 400; color: var(--white); }
  .avatar {
    position: absolute; width: 140px; height: 140px; border-radius: 50%;
    border: 3px solid var(--white); box-shadow: 0 0 0 3px var(--purple), 0 0 0 5px rgba(255,255,255,0.7);
  }
  .quote { position: absolute; top: 1918px; width: 300px; color: var(--white); font-size: 14px; line-height: 21px; font-style: italic; }
  .author { position: absolute; top: 2015px; color: var(--white); font-size: 15px; }

  /* Footer */
  .footer { position: absolute; left: 0; top: 2141px; width: 1200px; height: 345px; background: var(--footer-bg); }
  .brand-footer { position: absolute; left: 133px; top: 2226px; font-size: 32px; color: #8c8c8c; letter-spacing: 1px; }
  .foot-col h4 { position: absolute; font-size: 19px; font-weight: 400; color: var(--purple); text-transform: uppercase; }
  .foot-col a { position: absolute; font-size: 13.5px; color: #7a7a7a; text-decoration: none; }
  .contact-line { position: absolute; left: 807px; font-size: 13.5px; color: var(--ink); }
  .social { position: absolute; top: 2338px; width: 31px; height: 31px; border-radius: 50%; border: 1.5px solid var(--purple); background: var(--white); }
  .foot-rule { position: absolute; left: 129px; top: 2426px; width: 948px; height: 1px; background: #cfcfcf; }
  .copyright { position: absolute; top: 2446px; left: 0; width: 1200px; text-align: center; font-size: 12.5px; color: #6f6f6f; }
</style>
</head>
<body>

  <!-- Hero -->
  <section class="hero" role="img" aria-label="Close-up photograph of a stylist cutting hair with comb and scissors"></section>
  <nav class="nav">
    <a style="left:124px">Home</a><span class="sep" style="left:194px"></span>
    <a style="left:214px">About Us</a><span class="sep" style="left:318px"></span>
    <a style="left:337px">Services</a>
    <a style="left:729px">Price</a><span class="sep" style="left:794px"></span>
    <a style="left:814px">Product</a><span class="sep" style="left:913px"></span>
    <a style="left:933px">Contact</a>
  </nav>
  <div class="brand-hero">Corsetresses</div>
  <h1 class="hero-title">PRIVATE LUXURY HAIR SALON<br>IN AUSTRALIA</h1>
  <div class="dots" style="left:547px; top:533px;">
    <span class="off"></span><span></span><span></span><span></span>
  </div>

  <!-- Who we are -->
  <div class="who-photo" role="img" aria-label="Portrait photograph of a woman with long curly golden-brown hair"></div>
  <h2 class="section-title who-title">WHO WE ARE</h2>
  <p class="who-text">Maecenas aliquet velit vel turpis Mauris neque metus malesuada nec ultricies sit amet porttitor mattis enim In massa libero interdum nec interdum vel blandit sed nulla In ullamcorper est eget tempor cursus neque mi consectetuer mi a ultricies massa est sed nisl Class aptent taciti sociosqu ad litora torquent per conubia nostra per</p>
  <div class="btn-read">READ MORE</div>

  <!-- What we offer -->
  <svg class="abs" style="left:0; top:991px" width="1200" height="430" viewBox="0 0 1200 430" aria-hidden="true">
    <path d="M0 0 H1200 V370 Q600 480 0 370 Z" fill="var(--band-grey)"/>
  </svg>
  <h2 class="offer-title">WHAT WE OFFER</h2>

  <div class="offer-card" style="left:111px; background:linear-gradient(135deg,#6b6b6b,#2e2e2e);" role="img" aria-label="Photograph of hair being cut with scissors">
    <div class="name">Hair Cuts</div>
    <div class="desc">At vero eos et accusamus et iusto odiod<br>ignissimos ducimus qui blandit</div>
    <div class="link">CLICK HERE</div>
  </div>
  <div class="offer-card" style="left:437px; background:linear-gradient(135deg,#5a3a3a,#2a1f22);" role="img" aria-label="Photograph of freshly coloured hair">
    <div class="name">Colouring</div>
    <div class="desc">At vero eos et accusamus et iusto odiod<br>ignissimos ducimus qui blandit</div>
    <div class="link">CLICK HERE</div>
  </div>
  <div class="offer-card" style="left:762px; background:linear-gradient(135deg,#6e5836,#1f1a14);" role="img" aria-label="Photograph of a woman with long hair extensions">
    <div class="name">Extensions</div>
    <div class="desc">At vero eos et accusamus et iusto odiod<br>ignissimos ducimus qui blandit</div>
    <div class="link">CLICK HERE</div>
  </div>

  <svg class="arrow" style="left:107px; border-radius:0 28px 28px 0;" viewBox="0 0 34 56" aria-hidden="true">
    <path d="M21 20 L13 28 L21 36" fill="none" stroke="#333" stroke-width="2.5"/>
  </svg>
  <svg class="arrow" style="left:1053px; border-radius:28px 0 0 28px;" viewBox="0 0 34 56" aria-hidden="true">
    <path d="M13 20 L21 28 L13 36" fill="none" stroke="#333" stroke-width="2.5"/>
  </svg>

  <!-- Products -->
  <h2 class="section-title products-title">OUR PRODUCTS</h2>
  <p class="products-text">Maecenas aliquet velit vel turpis Mauris neque metus malesuada nec ultricies sit amet porttitor mattis enim In massa libero interdum nec interdum vel blandit sed nulla</p>
  <div class="btn-outline">View More Products</div>
  <div class="products-shelf" role="img" aria-label="Row of hair care product bottles and sprays"></div>

  <!-- Testimonials -->
  <svg class="abs" style="left:0; top:1780px" width="1200" height="362" viewBox="0 0 1200 362" aria-hidden="true">
    <path d="M0 52 Q600 -40 1200 52 V362 H0 Z" fill="var(--purple)"/>
  </svg>
  <h2 class="testi-title">TESTIMONIALS</h2>

  <div class="avatar" style="left:140px; top:1908px; background:linear-gradient(150deg,#3a2a26,#8a6a55 60%,#c9a48a);" role="img" aria-label="Portrait photograph of a woman with a dark bob haircut"></div>
  <p class="quote" style="left:288px;">Aociosqu ad litora torquent per conubia nostra per inceptos hymenaeos Proin nulla arcu nonummy luctus dictum eget fermen-tum et lorem Nunc convallis</p>
  <div class="author" style="left:284px;">- By Author Name</div>

  <div class="avatar" style="left:618px; top:1908px; background:linear-gradient(150deg,#e6c9a8,#c49466 60%,#8c6240);" role="img" aria-label="Portrait photograph of a woman with long wavy blonde hair"></div>
  <p class="quote" style="left:765px;">Aociosqu ad litora torquent per conubia nostra per inceptos hymenaeos Proin nulla arcu nonummy luctus dictum eget fermen-tum et lorem Nunc convallis</p>
  <div class="author" style="left:761px;">- By Author Name</div>

  <div class="dots" style="left:568px; top:2087px;">
    <span class="off" style="border-color:#4a1f45;"></span>
    <span style="background:#4a1f45;border-color:#4a1f45;"></span>
    <span style="background:#4a1f45;border-color:#4a1f45;"></span>
  </div>

  <!-- Footer -->
  <footer class="footer"></footer>
  <div class="brand-footer">Corsetresses</div>

  <div class="foot-col">
    <h4 style="left:393px; top:2188px;">Company</h4>
    <a style="left:393px; top:2228px;">About Us</a>
    <a style="left:393px; top:2256px;">What We Do</a>
    <a style="left:393px; top:2284px;">Pricing</a>
    <a style="left:393px; top:2312px;">Services</a>

    <h4 style="left:596px; top:2188px;">Resources</h4>
    <a style="left:596px; top:2228px;">Our Products</a>
    <a style="left:596px; top:2256px;">Testimonials</a>
    <a style="left:596px; top:2284px;">Contact Us</a>
    <a style="left:596px; top:2312px;">FAQ</a>

    <h4 style="left:807px; top:2186px;">Contact Us</h4>
  </div>
  <div class="contact-line" style="top:2226px;">412 Marlow Avenue Suite B12</div>
  <div class="contact-line" style="top:2251px;">Eastbrook, PA 19120</div>
  <div class="contact-line" style="top:2276px;">(555) 214-3080</div>
  <div class="contact-line" style="top:2301px;">info@companyname.com</div>

  <span class="social" style="left:807px;"></span>
  <span class="social" style="left:843px;"></span>
  <span class="social" style="left:879px;"></span>
  <span class="social" style="left:915px;"></span>

  <div class="foot-rule"></div>
  <div class="copyright">© 2017 Company Name&nbsp; All right reserved&nbsp; Term of Use</div>

</body>
</html>
```